Merrowin Vodka logo and label design

We would like a logo and bottle label design for a new line of Ultra-Premium Vodka. The Company is called Merrowin Spirits and is based in Brisbane, Australia. We would like a 'Gatsby/Prohibition era vibe to the design. We want to keep it minimalistic and sleek. We strongly prefer a minimalist design and colour palette. Black,Gold,Grey,White,Silver,Red and Blue

The bottle will be similar in shape to Castellane/Blue Heron. There will also need to be space on the label for required information, as well as short bio of the company, which will be provided to the winning design.
Updates

We would like to add the polish code of arms for Opoczno. Have attached link for reference. https://www.crestarchive-demo.net/crestwiki/index.php?title=Opoczno

Target Market(s)

Luxury brand customers

Logo Text

Merrowin Ultra-Premium Vodka

Logo styles of interest
Wordmark Logo
Lettermark Logo
Requirements
Must have
• This is the first release from our new Vodka label. We want a logo and bottle label that reflects a premium product. We very much like Prohibition/Gatsby era themed bottles and labels. The label and bottle should be elegant and clean.
Should not have
• Anything too busy or confusing.

```html
<!DOCTYPE html>
<html lang="en">
<head>
<meta charset="utf-8">
<title>Merrowin Ultra-Premium Vodka – Bottle Label</title>
<link rel="stylesheet" href="https://fonts.googleapis.com/css2?family=Josefin+Sans:wght@600&display=swap">
<style>
  :root {
    --page: #ffffff;
    --label-edge: #0b0b0c;
    --label-sheen: #343434;
    --gold: #d8b45e;
  }
  html, body {
    margin: 0;
    padding: 0;
    width: 984px;
    height: 1200px;
    overflow: hidden;
    background: var(--page);
  }
  .canvas {
    position: relative;
    width: 984px;
    height: 1200px;
  }
  .label {
    position: absolute;
    left: 132px;
    top: 180px;
    width: 720px;
    height: 840px;
  }
  .label-shape {
    position: absolute;
    inset: 0;
    display: block;
  }
  .label-wordmark {
    position: absolute;
    left: 0;
    right: 0;
    top: 262px;
    text-align: center;
  }
  .brand-name {
    margin: 0;
    font-family: "Josefin Sans", sans-serif;
    font-weight: 600;
    font-size: 72px;
    line-height: 1;
    letter-spacing: 0.1em;
    padding-left: 0.1em;
    color: var(--gold);
  }
  .brand-descriptor {
    margin: 20px 0 0;
    font-family: "Josefin Sans", sans-serif;
    font-weight: 600;
    font-size: 21px;
    line-height: 1;
    letter-spacing: 0.36em;
    padding-left: 0.36em;
    color: var(--gold);
  }
</style>
</head>
<body>
  <main class="canvas">
    <section class="label">
      <svg class="label-shape" viewBox="0 0 720 840" width="720" height="840" aria-hidden="true">
        <defs>
          <linearGradient id="labelSheen" x1="0" y1="0" x2="1" y2="0">
            <stop offset="0" stop-color="#0b0b0c"/>
            <stop offset="0.55" stop-color="#343434"/>
            <stop offset="1" stop-color="#0b0b0c"/>
          </linearGradient>
        </defs>
        <path d="M0 0 H720 V480 A360 360 0 0 1 0 480 Z" fill="url(#labelSheen)"/>
      </svg>
      <div class="label-wordmark">
        <h1 class="brand-name">MERROWIN</h1>
        <p class="brand-descriptor">ULTRA-PREMIUM VODKA</p>
      </div>
    </section>
  </main>
</body>
</html>
```